Create Stationary from existing logo(s)

We are looking for some assistance in tidying up the stationary that supports our brand. We are an innovative technology company, generally working with larger corporates. We have previously done a little work on brochures etc, but never really pulled it all together with our stationary.
In particular I am looking for:
1. A4 Letter Template for Letter (Microsoft Word 2007 template format)
2. A4 Template for Reports (Microsoft Word 2007 template format). This should include title page, table of contents, subsequent report pages including styles for tables, headings, and text.
3. Business Card Design - we will need to be able to edit the text, so the card should include sample text for name, title, phone number, mobile number, and email address.
4. Presentation Template (Microsoft Powerpoint 2007 template). See attached powerpoint which we quite like, but isn't really a template, and we have don't really use any consistent styles in it. The Powerpoint template needs to have a cover / title page, section break pages, and pages that may contain bullet point text, pictures, or a combination of bullet point text and pictures. We do like our current presentation, which gives some indication of our thinking.
I am attaching a brochure and the powerpoint presentation to give some indication of current materials. We are happy with the main concepts behind the brochure, and would not really be looking to change the key concepts unless you have a compelling reason. We do like the use of this secondary logo in the stationary related items
I have uploaded an eps file of the logo.

```html
<!DOCTYPE html>
<html lang="en">
<head>
<meta charset="utf-8">
<title>Veltrix Systems – Letterhead</title>
<link rel="stylesheet" href="https://fonts.googleapis.com/css2?family=PT+Sans:wght@400;700&display=swap">
<style>
  :root {
    --brand-blue: #1b3a9e;
    --ink: #3a3a3a;
    --paper: #ffffff;
    --backdrop: #ffffff;
    --edge: #d4d4d4;
    --ghost: #e3e3e3;
  }
  * { box-sizing: border-box; margin: 0; padding: 0; }
  html, body {
    width: 1200px; height: 826px; overflow: hidden;
    background: var(--backdrop);
    font-family: "PT Sans", sans-serif;
  }
  .sheet-set { position: relative; width: 1200px; height: 826px; }
  .letterhead {
    position: absolute; top: 11px;
    width: 560px; height: 804px;
    background: var(--paper);
    border: 1px solid var(--edge);
    box-shadow: 3px 4px 6px rgba(0,0,0,0.18);
    overflow: hidden;
  }
  .letterhead--first { left: 24px; }
  .letterhead--follow { left: 619px; }

  .brand-name {
    position: absolute; top: 34px; right: 22px;
    display: flex; align-items: center; gap: 8px;
    font-size: 22px; font-weight: 700; color: var(--brand-blue);
    line-height: 1;
  }
  .brand-name__mark {
    width: 16px; height: 16px; background: var(--brand-blue);
  }

  .ghost-name {
    position: absolute; top: 355px; left: 0; width: 100%;
    text-align: center;
    font-size: 30px; font-weight: 700; color: var(--ghost);
  }

  .sender {
    position: absolute; left: 40px; bottom: 22px;
    font-size: 8px; line-height: 11px; color: var(--ink);
    font-style: normal;
  }
  .letterhead--follow .sender { left: 32px; bottom: 30px; }
  .sender-rule {
    position: absolute; left: 0; bottom: 30px;
    width: 14px; height: 82px; background: var(--brand-blue);
  }

  .web {
    position: absolute; right: 26px; bottom: 14px;
    font-size: 10px; color: var(--brand-blue);
  }
  .letterhead--follow .web { bottom: 22px; }

  .foot-band {
    position: absolute; left: 0; bottom: 0;
    width: 100%; height: 6px; background: var(--brand-blue);
  }
  .letterhead--follow .foot-band { height: 3px; }
</style>
</head>
<body>
<main class="sheet-set">

  <section class="letterhead letterhead--first">
    <div class="brand-name"><span class="brand-name__mark"></span>Veltrix Systems</div>
    <address class="sender">
      Level 4, 118 Harbour Lane<br>
      Sydney, 2000<br>
      Australia<br>
      P +61 2 5550 1234<br>
      F +61 2 5550 5678<br>
      E info@veltrixsystems.com.au
    </address>
    <div class="web">www.veltrixsystems.com.au</div>
    <div class="foot-band"></div>
  </section>

  <section class="letterhead letterhead--follow">
    <div class="brand-name"><span class="brand-name__mark"></span>Veltrix Systems</div>
    <div class="ghost-name">Veltrix Systems</div>
    <div class="sender-rule"></div>
    <address class="sender">
      Level 4, 118 Harbour Lane<br>
      Sydney 2000<br>
      Australia<br>
      P +61 2 5550 1234<br>
      F +61 2 5550 5678<br>
      E info@veltrixsystems.com.au
    </address>
    <div class="web">www.veltrixsystems.com.au</div>
    <div class="foot-band"></div>
  </section>

</main>
</body>
</html>
```